Business Cards Design for the electrical wholesaler: clean bold dynamic :)

We need a business card design that would follow our latest brand guidelines. As an electrical wholesaler we want to bring a fresh look and feel into the industry. The design should be clean bold and dynamic. It should come alive with the renewed energy of our green colour. Our grey colour should keep things balanced and complement the notion of maturity and responsibility. We employ Lato as a corporate font however are not bound by this font and we’re open to interpretation here.

Target Market(s)

Electrical contractors

Industry/Entity Type

Business

Contact Information for Business Card

Logo
Name & Surname: Halyna Dorosh
Job Title: Director of Marketing
Email: halya.dorosh@quillmail.example
Cell phone: XXX.XXX.XXXX
Address: 20517 - 87 Ave. Edmonton, AB, Canada. T6K 4N8
Business Phone: 780.555.0184
Website: www.brovix.example

Font styles to use
Other font styles liked:
• Lato

Requirements
Must have
• Logo & website
Nice to have
• Brand elements - some of them you may find in the attached Brand Guidelines (e.g. three lines on the background signifying "W")

```html
<!DOCTYPE html>
<html lang="en">
<head>
<meta charset="utf-8">
<title>Brovix business cards</title>
<link href="https://fonts.googleapis.com/css2?family=Lato:wght@400;700;900&display=swap" rel="stylesheet">
<style>
  :root {
    --green: #7dbb2f;
    --grey-dark: #4a4b4d;
    --grey-band: #47484a;
    --ink: #3c3d3f;
    --rule: #9a9a9a;
    --backdrop: #9b9b9b;
    --paper-top: #ffffff;
    --paper-bottom: #ececec;
  }
  * { box-sizing: border-box; margin: 0; padding: 0; }
  html, body { width: 1200px; height: 900px; overflow: hidden; }
  body {
    background: var(--backdrop);
    font-family: "Lato", Arial, sans-serif;
    position: relative;
  }
  .card {
    position: absolute;
    left: 270px;
    width: 660px;
    height: 377px;
    border-radius: 18px;
    overflow: hidden;
    box-shadow: 0 10px 24px rgba(0,0,0,0.28);
  }

  /* Back */
  .card-back { top: 48px; background: var(--grey-dark); }
  .card-back .brand {
    position: absolute; left: 0; right: 0; top: 140px;
    display: flex; justify-content: center; align-items: center; gap: 14px;
  }
  .brand-dot { width: 34px; height: 34px; border-radius: 50%; background: var(--green); }
  .card-back .brand-name { font-size: 64px; font-weight: 700; color: #ffffff; line-height: 1; letter-spacing: -1px; }
  .card-back .site {
    position: absolute; left: 0; right: 0; top: 250px;
    text-align: center; font-size: 18px; letter-spacing: 3px; color: #ffffff;
  }
  .card-back .site em { font-style: normal; color: var(--green); }

  /* Front */
  .card-front {
    top: 475px;
    background: linear-gradient(160deg, var(--paper-top) 0%, var(--paper-bottom) 100%);
    color: var(--ink);
  }
  .card-front .brand {
    position: absolute; left: 44px; top: 40px;
    display: flex; align-items: center; gap: 12px;
  }
  .card-front .brand-name { font-size: 58px; font-weight: 700; color: var(--ink); line-height: 1; letter-spacing: -1px; }
  .rule-long { position: absolute; left: 44px; right: 40px; top: 122px; height: 1px; background: var(--rule); }
  .person { position: absolute; left: 44px; top: 136px; }
  .person-name { font-size: 30px; font-weight: 900; color: var(--green); line-height: 1.1; }
  .person-title { font-size: 18px; color: var(--ink); margin-top: 2px; }
  .rule-short { width: 200px; height: 1px; background: var(--rule); margin-top: 10px; }
  .contacts { position: absolute; left: 44px; top: 226px; list-style: none; font-size: 16px; }
  .contacts li { display: flex; align-items: center; gap: 10px; height: 23px; }
  .contacts svg { width: 16px; height: 16px; flex: none; }
  .address {
    position: absolute; right: 40px; top: 150px;
    text-align: right; font-size: 16px; line-height: 1.4; font-style: normal;
  }
  .bands { position: absolute; left: 0; top: 0; width: 660px; height: 377px; }
  .bands .site { font-family: "Lato", Arial, sans-serif; font-size: 17px; fill: #ffffff; letter-spacing: 1px; }
</style>
</head>
<body>

<section class="card card-back" aria-label="Card back">
  <div class="brand">
    <span class="brand-dot"></span>
    <span class="brand-name">brovix</span>
  </div>
  <p class="site">www.<em>brovix</em>.example</p>
</section>

<section class="card card-front" aria-label="Card front">
  <svg class="bands" viewBox="0 0 660 377" aria-hidden="true">
    <polygon points="0,338 660,338 660,377 0,377" fill="var(--grey-band)"/>
    <polygon points="420,300 600,300 620,338 440,338" fill="var(--grey-band)"/>
    <polygon points="440,300 595,300 612,332 456,332" fill="var(--green)"/>
    <polygon points="610,300 660,300 660,338 630,338" fill="var(--grey-band)"/>
    <text class="site" x="530" y="322" text-anchor="middle">www.brovix.example</text>
  </svg>

  <div class="brand">
    <span class="brand-dot"></span>
    <span class="brand-name">brovix</span>
  </div>
  <div class="rule-long"></div>

  <div class="person">
    <h1 class="person-name">Halyna Dorosh</h1>
    <p class="person-title">Director of Marketing</p>
    <div class="rule-short"></div>
  </div>

  <ul class="contacts">
    <li>
      <svg viewBox="0 0 16 16"><rect x="4" y="1" width="8" height="14" rx="1.5" fill="none" stroke="var(--green)" stroke-width="1.6"/></svg>
      780.555.0184
    </li>
    <li>
      <svg viewBox="0 0 16 16"><path d="M3 2 L6 2 L7 5 L5.5 6.5 Q7 9.5 9.5 10.5 L11 9 L14 10 L14 13 Q8 14 2.5 7.5 Q2 4 3 2 Z" fill="var(--green)"/></svg>
      780.555.0184
    </li>
    <li>
      <svg viewBox="0 0 16 16"><rect x="1" y="3" width="14" height="10" fill="var(--green)"/><path d="M1 3 L8 9 L15 3" fill="none" stroke="#ffffff" stroke-width="1.2"/></svg>
      halya.dorosh@quillmail.example
    </li>
  </ul>

  <address class="address">20517 - 87 Ave. Edmonton<br>AB, Canada. T6K 4N8</address>
</section>

</body>
</html>
```